Valdo Capital

We need a corporate style website design for a new company based in Shenzhen's Qianhai Special Economic Development Zone, China. We provide a range of financial services to large international investment companies. Typically these companies invest over 5 million RMB. The company is part of a group that consists of NorthKilns, ValdoTrusts and ValdoEquity. Our location and gateway into Qianhai Special Economic Zone is our core advantage. We would like to see designs that Do Not use purple and orange. The website design should be similar to other websites in this family but different enough to give it a unique style (See attached website links for reference). The final design should communicate financial safety and growth. This website will act partly as a business chamber with connections to the government so we would like it to be diplomatic in style.

www.northkilns.example
www.valdotrusts.example

*Nevegation Bar
Should including Homepage, Financial Product, Team, News.
Could refer to www.valdotrusts.example

*Contact Details

Miss Lan
Address:E 728, North Block, KMO Centre, East Sector, Shenzhen Bright Science Campus
Telephone: +86 0755 63920417
Cellphone: +86 13957280316

* Social Media
Should be grouped like:
1. Weibo QRcode+ Weibo
2. Facebook, Twitter, Linkedin.

Industry/Entity Type

Investment

```html
<!DOCTYPE html>
<html lang="en">
<head>
<meta charset="utf-8">
<title>Valdo Capital</title>
<link rel="stylesheet" href="https://fonts.googleapis.com/css2?family=Open+Sans:wght@300;400;600;700&family=Raleway:wght@400;500&display=swap">
<style>
:root{
  --blue:#2a9fd8;
  --blue-dark:#1b7fb3;
  --ink:#333;
  --muted:#8a8a8a;
  --light:#f4f4f4;
  --line:#dcdcdc;
  --nav:#1c1c1c;
  --footer:#141414;
  --teal:#5bbcb8;
}
*{box-sizing:border-box;margin:0;padding:0}
html,body{width:1200px;height:2347px;overflow:hidden;background:#fff}
body{font-family:"Open Sans",Arial,sans-serif;color:var(--ink);position:relative}
.abs{position:absolute}

/* header */
.site-header{position:absolute;left:0;top:0;width:1200px;height:146px;background:#fff}
.brand{position:absolute;left:110px;top:42px;display:flex;align-items:center;gap:10px}
.brand-mark{width:50px;height:50px;border:5px solid var(--blue);border-radius:2px}
.brand-name{font-family:"Raleway",sans-serif;font-size:21px;line-height:25px;color:#222;letter-spacing:1px}
.brand-name small{font-size:12px;color:var(--blue)}
.lang{position:absolute;left:935px;top:44px;font-size:15px;color:#222;display:flex;align-items:center;gap:10px}
.lang .caret{color:var(--blue);font-size:12px}
.social-top{position:absolute;left:913px;top:80px;width:190px;height:40px;background:#f2f2f2;border-radius:3px;display:flex;align-items:center;justify-content:center;gap:6px}
.social-top span{width:26px;height:26px;border-radius:50%;background:#bdbdbd}
.social-top span.active{background:var(--blue)}

/* nav */
.main-nav{position:absolute;left:0;top:146px;width:1200px;height:50px;background:linear-gradient(#2c2c2c,#111);display:flex;padding-left:94px}
.main-nav a{color:#fff;text-decoration:none;font-size:15px;letter-spacing:1px;line-height:50px;padding:0 16px;border-right:1px solid #3a3a3a}
.main-nav a:last-child{border-right:0}

/* hero */
.hero{position:absolute;left:0;top:196px;width:1200px;height:558px;background:linear-gradient(170deg,#9cc3e6 0%,#d7e6f3 45%,#eef3f8 70%,#c9d9ea 100%)}
.hero-caption{position:absolute;left:110px}
.cap-line{position:absolute;left:0;background:rgba(30,30,30,.9);color:#fff;font-size:30px;font-weight:300;white-space:nowrap;padding:0 10px;line-height:49px}
.cap-line b{font-weight:700}
.cap-blue{position:absolute;left:0;background:var(--blue);color:#fff;font-size:17px;line-height:52px;padding:0 20px;width:594px}
.btn{display:inline-block;background:var(--blue);color:#fff;font-size:14px;text-align:center;border-bottom:3px solid var(--blue-dark);border-radius:2px}
.dots{position:absolute;left:110px;top:416px;display:flex;gap:8px;align-items:center}
.dots i{width:9px;height:9px;border-radius:50%;background:var(--blue)}
.dots i.on{width:13px;height:13px;background:#222}

/* welcome */
.section-title{position:absolute;left:0;width:1200px;text-align:center;font-weight:300;color:#777;font-size:31px}
.section-title em{font-style:normal;color:var(--blue)}
.lead{position:absolute;left:140px;width:920px;text-align:center;font-weight:300;color:var(--muted);font-size:16px;line-height:28px}

/* features */
.feature{position:absolute;top:1075px;width:270px;text-align:center}
.feature-photo{width:270px;height:224px;border-radius:5px;box-shadow:0 2px 4px rgba(0,0,0,.25)}
.feature h3{font-family:"Raleway",sans-serif;font-weight:500;font-size:17px;margin-top:22px;color:#222}
.feature p{font-family:Arial,sans-serif;font-size:13px;line-height:22px;color:#444;margin-top:6px}

/* news band */
.news-band{position:absolute;left:0;top:1483px;width:1200px;height:310px;background:var(--light);border-bottom:3px solid var(--line)}
.block-head{position:absolute;font-size:16px;font-weight:600;color:#222;padding-bottom:10px;border-bottom:3px solid #e2e2e2}
.arrows{position:absolute;right:0;top:0;display:flex;gap:4px}
.arrows span{width:18px;height:18px;background:var(--teal);color:#fff;font-size:12px;line-height:18px;text-align:center}
.post-title{position:absolute;left:383px;top:1570px;font-size:17px;color:#333}
.post-meta{position:absolute;left:383px;top:1612px;font-size:11px;line-height:20px;color:#aaa;font-weight:600}
.post-excerpt{position:absolute;left:383px;top:1660px;font-size:14px;line-height:20px;color:#333;width:230px}
.quote{position:absolute;left:829px;top:1560px;width:230px;font-size:14px;line-height:21px;color:#444}
.quote a{color:var(--teal);font-size:10px;font-weight:700;text-decoration:none}
.avatar{position:absolute;left:829px;top:1650px;width:64px;height:64px;border-radius:50%;background:linear-gradient(#a88d7a,#7a5e4c)}
.person{position:absolute;left:908px;top:1651px;font-size:16px;color:#333}
.person small{display:block;font-size:11px;color:#555;margin-top:4px}

/* clients */
.clients{position:absolute;left:0;top:2050px;width:1200px;display:flex;justify-content:space-around;padding:0 70px}
.client{font-size:26px;font-weight:700;color:#444;display:flex;align-items:center;gap:10px}
.client i{width:22px;height:22px;border-radius:50%;background:#444;display:block}

/* footer */
.site-footer{position:absolute;left:0;top:2258px;width:1200px;height:89px;background:var(--footer)}
.footer-brand{position:absolute;left:108px;top:16px;display:flex;align-items:center;gap:10px}
.footer-brand .brand-mark{border-color:#777;width:44px;height:50px}
.footer-brand .brand-name{color:#888;font-size:19px}
.footer-brand .brand-name small{color:#888}
.copyright{position:absolute;left:418px;top:36px;font-size:12px;color:#888}
.follow{position:absolute;left:986px;top:14px;color:#ddd;font-size:17px}
.follow-icons{position:absolute;left:981px;top:44px;display:flex;gap:10px}
.follow-icons span{width:28px;height:28px;border-radius:50%;background:#3a3a3a}
</style>
</head>
<body>

<header class="site-header">
  <div class="brand">
    <div class="brand-mark"></div>
    <div class="brand-name">Valdo<br>Capital<small>.com</small></div>
  </div>
  <div class="lang">
    <svg width="30" height="20" viewBox="0 0 30 20"><ellipse cx="15" cy="10" rx="14" ry="9" fill="none" stroke="#2a9fd8" stroke-width="2"/><line x1="1" y1="10" x2="29" y2="10" stroke="#2a9fd8" stroke-width="2"/><line x1="15" y1="1" x2="15" y2="19" stroke="#2a9fd8" stroke-width="2"/></svg>
    <span>English (Uk)</span><span class="caret">▼</span>
  </div>
  <div class="social-top" aria-label="Social links">
    <span class="active"></span><span></span><span></span><span></span><span></span>
  </div>
</header>

<nav class="main-nav">
  <a>Home</a><a>About us</a><a>About Qianhai</a><a>Our Services</a><a>Expert Team</a><a>Partners</a><a>Contact Us</a>
</nav>

<section class="hero" role="img" aria-label="Businessman holding a laptop among tall glass towers under a cloudy sky">
  <div class="hero-caption" style="top:187px">
    <div class="cap-line" style="top:0;width:331px">VALDO TRUSTS</div>
    <div class="cap-line" style="top:49px;width:618px">A <b>INTEGRATE</b>, SUPERIOR <b>RESOURCES OF US</b></div>
    <div class="cap-blue" style="top:100px">Limited Shenzhen, located in Qianhai, China, is a new real-estate project</div>
    <a class="btn" style="position:absolute;top:163px;width:133px;line-height:40px">MORE DETAILS</a>
  </div>
  <div class="dots"><i></i><i></i><i class="on"></i></div>
</section>

<h2 class="section-title" style="top:808px">Wel Come Valdo Capital Take A <em>Second And Explore it</em></h2>
<p class="lead" style="top:864px">Lorem ipsum dolor sit amet, consectetur adipiscing elit. Fusceelementum, nulla vel pellentesque consequat, ante nulla hendrerit arcu, ac tincidunt mauris lacus sed leo. vamus suscipit molestie vestibulum. Integer elementum congue.</p>
<a class="btn abs" style="left:512px;top:947px;width:137px;line-height:37px;font-size:12px">CONATCT US NOW</a>

<div class="feature" style="left:110px">
  <div class="feature-photo" role="img" aria-label="Office tower seen from below against the sky" style="background:linear-gradient(135deg,#2f5f9a,#b9c4cf 55%,#3a5575)"></div>
  <h3>DOCUMENTS</h3>
  <p>Sed ut perspiciatis unde omnis iste<br>natus error sit voluptatem accusantium<br>doloremque laudantium, totam rem</p>
</div>
<div class="feature" style="left:444px">
  <div class="feature-photo" role="img" aria-label="Business team reviewing papers around a glass table" style="background:linear-gradient(135deg,#3b3b3b,#9a9a9a 50%,#2c2c2c)"></div>
  <h3>GET A QUOTE</h3>
  <p>Sed ut perspiciatis unde omnis iste<br>natus error sit voluptatem accusantium<br>doloremque laudantium, totam rem</p>
</div>
<div class="feature" style="left:820px">
  <div class="feature-photo" role="img" aria-label="Trading desk with many financial monitors" style="background:linear-gradient(180deg,#e9ecef,#5d7896 50%,#6b4a32)"></div>
  <h3>PRINT LIST OF RECIPIENTS</h3>
  <p>Sed ut perspiciatis unde omnis iste<br>natus error sit voluptatem accusantium<br>doloremque laudantium, totam rem</p>
</div>

<section class="news-band">
  <div class="block-head" style="left:114px;top:31px;width:540px">RECENT POSTS
    <div class="arrows"><span>+</span><span>‹</span><span>›</span></div>
  </div>
  <div class="abs" role="img" aria-label="Desk with laptop, notebook and stationery" style="left:114px;top:88px;width:254px;height:170px;background:linear-gradient(135deg,#c9a27a,#e9e3da 50%,#b4845c)"></div>
  <div class="block-head" style="left:829px;top:31px;width:255px">TESTIMONIALS
    <div class="arrows"><span>‹</span><span>›</span></div>
  </div>
</section>
<div class="post-title">Another Post with Everything</div>
<div class="post-meta">SEPTEMBER 17,2008 / GENERAL NEWS<br>TECHNOLOGY / 3 COMMENTS</div>
<p class="post-excerpt">Lorem ipsum dolor sit amet, consectetuer adipiscing elit. Curabitur quam augue, vehicula quis....</p>
<p class="quote">There are many variations of passages of Lorem Ipsum available, but the majority have suffered....<a>READ MORE</a></p>
<div class="avatar" role="img" aria-label="Portrait of the client"></div>
<div class="person">Marta Kellin<small>Designer</small></div>

<h2 class="section-title" style="top:1830px">Our <em>Clients</em></h2>
<p class="lead" style="top:1880px">Lorem ipsum dolor sit amet, consectetur adipiscing elit. Fusceelementum, nulla vel pellentesque consequat, ante nulla hendrerit arcu, ac tincidunt mauris lacus sed leo. vamus suscipit molestie vestibulum. Integer elementum congue.</p>
<div class="clients">
  <div class="client">Norbridge</div>
  <div class="client">Elmspan</div>
  <div class="client"><i></i>Tessaro</div>
  <div class="client">Quillworks</div>
  <div class="client">Arvane</div>
</div>

<footer class="site-footer">
  <div class="footer-brand">
    <div class="brand-mark"></div>
    <div class="brand-name">Valdo<br>Capital<small>.com</small></div>
  </div>
  <div class="copyright">© Copyright 2013 by Ostra Studio. All Rights Reserved.</div>
  <div class="follow">Follow Us</div>
  <div class="follow-icons"><span></span><span></span><span></span></div>
</footer>

</body>
</html>
```